Modernize Police Fraternity Website

We're in search of a web developer to rejuvenate the digital presence of our co-ed fraternity at Ferndale Ridge State, which is dedicated to supporting students pursuing careers in criminal justice and law enforcement. We aim for a modern, minimalist website that's both user-friendly and simple to maintain. Key features will include an inviting landing page, an easy-to-use contact form, and a secure online store for handling memberships, donations, and sales of items like t-shirts. While we're eager to retain as much of our existing content as possible, we're also open to thoughtful content adjustments to elevate our design. For a glimpse of our current website and to understand our mission, please visit taurhokappa.org.

Target Market(s)

Students

Coding

Coded - Design and coding required

Number of Pages Required

4 page

Font styles to use
Serif

Colors

Designer to choose colors to be used in the design.

Requirements
Must have
• Landing page, contact us, shop
Nice to have
• membership tracking

```html
<!DOCTYPE html>
<html lang="en">
<head>
<meta charset="utf-8">
<title>Tau Rho Kappa Fraternity</title>
<link rel="stylesheet" href="https://fonts.googleapis.com/css2?family=Bodoni+Moda:wght@400;500&family=Poppins:ital,wght@0,400;0,500;0,700;1,400&family=Homemade+Apple&display=swap">
<style>
:root{
  --green:#1f3b38;
  --green-dark:#1c3431;
  --red:#a3150a;
  --red-deep:#7a1408;
  --mint:#f1f8f7;
  --grey:#e8e8e8;
  --ink:#2a2a2a;
  --line:#c9cfcf;
}
*{margin:0;padding:0;box-sizing:border-box}
html,body{width:1200px;height:4520px;overflow:hidden}
body{position:relative;background:var(--mint);font-family:'Poppins',sans-serif;color:var(--ink)}
.abs{position:absolute}
.serif{font-family:'Bodoni Moda',serif;font-weight:400}
.photo{position:absolute}

/* nav */
.nav{left:0;top:0;width:1200px;height:74px;background:rgba(31,59,56,.85);z-index:3}
.brand{left:212px;top:14px;display:flex;align-items:center;gap:8px;color:#fff;font-family:'Poppins',sans-serif;font-size:15px;font-weight:500;letter-spacing:2px}
.brand i{width:44px;height:44px;border-radius:50%;border:2px solid var(--red);display:block}
.menu{left:570px;top:26px;display:flex;gap:32px;font-size:11.5px;color:#fff;font-weight:500}
.join{left:901px;top:21px;width:102px;height:28px;background:var(--red);border-radius:14px;color:#fff;font-size:11.5px;font-weight:700;text-align:center;line-height:28px}

/* hero */
.hero{left:0;top:0;width:1200px;height:575px;background:linear-gradient(180deg,#6f92b5 0%,#8a5a3e 45%,#3d4a2b 100%)}
.hero-title{left:0;top:240px;width:1200px;text-align:center;color:#fff;font-size:36px;letter-spacing:10px}
.hero-est{left:0;top:506px;width:1200px;text-align:center;color:#fff;font-size:20px;letter-spacing:6px}

/* welcome */
.h-wide{letter-spacing:8px;color:var(--ink)}
.welcome-h{left:205px;top:696px;font-size:32px}
.p{font-size:11.8px;line-height:21.5px;color:#333}
.welcome-p{left:205px;top:752px;width:430px}
.btn-out{border:1.5px solid var(--red);border-radius:14px;height:28px;font-size:11.5px;font-weight:500;color:var(--red);text-align:center;line-height:25px}
.welcome-btn{left:205px;top:1057px;width:150px}
.divider{left:205px;top:1114px;width:430px;height:1px;background:var(--line)}
.social-label{left:205px;top:1135px;font-size:11.5px;color:#333;letter-spacing:.5px}
.socials{display:flex;gap:11px}
.socials span{width:32px;height:32px;border-radius:50%;border:1.5px solid var(--red);display:block}
.welcome-social{left:406px;top:1129px}
.frame{position:absolute;border:1.5px solid var(--red)}

/* strip */
.strip-word{left:240px;top:1400px;width:225px;text-align:center;color:#fff;font-size:26px;letter-spacing:5px}

/* careers */
.careers{left:0;top:1644px;width:1200px;height:575px;background:var(--grey)}
.careers-h{left:0;top:1680px;width:1200px;text-align:center;font-size:26px;letter-spacing:6px;color:var(--green)}
.card{position:absolute;width:363px;height:145px;border:1.5px solid #c4c4c4;background:var(--grey);text-align:center}
.card svg{margin-top:36px}
.card p{font-size:12.5px;font-weight:700;letter-spacing:1px;margin-top:12px;color:#222}

/* officers */
.officers-text{left:0;top:2460px;width:1200px;text-align:center;white-space:nowrap}
.officers-text .script{font-family:'Homemade Apple',cursive;color:var(--red);font-size:36px}
.officers-text .serif{color:#fff;font-size:34px;letter-spacing:7px}

/* support */
.support{left:0;top:2710px;width:1200px;height:412px;background:#ebebeb;box-shadow:0 8px 10px rgba(0,0,0,.08)}
.support-h{left:205px;top:2830px;font-size:28px}
.support-p{left:205px;top:2880px;width:320px}
.btn-red{background:var(--red);color:#fff;border-radius:16px;height:32px;font-size:11.5px;font-weight:700;text-align:center;line-height:32px}
.donate{left:205px;top:2970px;width:155px}

/* contact */
.contact-h{left:0;top:3196px;width:1200px;text-align:center;font-size:34px}
.contact-p{left:0;top:3256px;width:1200px;text-align:center}
.form{left:300px;top:3338px;width:607px;height:363px;border:1.5px solid #c8cfcf}
.field{position:absolute;left:367px;width:475px;height:28px;border-bottom:1px solid #d6dcdc;font-size:11.5px;color:#333;letter-spacing:.8px;padding-left:14px}
.send{left:367px;top:3617px;width:145px}

/* alumni */
.alumni{left:0;top:3754px;width:1200px;height:458px;background:var(--red-deep)}
.alumni-h{left:649px;top:3818px;font-size:30px;color:#fff;letter-spacing:8px}
.alumni-p{left:649px;top:3878px;width:356px;color:#fff;font-style:italic}
.sign{left:649px;color:#fff;font-family:'Homemade Apple',cursive;font-size:10.5px}
.alumni-btn{left:649px;top:4137px;width:148px;border-color:#fff;color:#fff}

/* footer */
.footer{left:0;top:4212px;width:1200px;height:308px;background:var(--green-dark)}
.foot-mark{left:577px;top:4250px;width:46px;height:46px;border-radius:50%;border:2px solid var(--red)}
.foot-name{left:0;top:4332px;width:1200px;text-align:center;color:#fff;font-size:22px;letter-spacing:5px}
.foot-col{position:absolute;top:4405px;width:200px;text-align:center;color:#fff}
.foot-col h4{font-weight:400;font-size:14px;letter-spacing:3px;margin-bottom:12px}
.foot-col p{font-size:11px;line-height:18px;color:#cfd8d6}
.foot-col .socials{justify-content:center}
.foot-col .socials span{border-color:#fff}
</style>
</head>
<body>

<header>
  <div class="abs hero" role="img" aria-label="Red brick university hall with turret and trees under a blue sky"></div>
  <div class="abs nav"></div>
  <div class="abs brand" style="z-index:4"><i></i>ΤΡΚ</div>
  <nav class="abs menu" style="z-index:4"><span>HOME</span><span>ABOUT US ▾</span><span>EVENTS</span><span>ALUMNI ▾</span></nav>
  <div class="abs join" style="z-index:4">JOIN US</div>
  <h1 class="abs hero-title serif">TAU RHO KAPPA FRATERNITY</h1>
  <div class="abs hero-est serif">EST. 1935</div>
</header>

<section class="welcome">
  <h2 class="abs serif h-wide welcome-h">WELCOME</h2>
  <div class="abs p welcome-p">
    <p>Tau Rho Kappa is the coeducational professional criminal justice fraternity at the acclaimed Ferndale Ridge State University in beautiful Ferndale Ridge, California.</p>
    <p style="margin-top:21px">Student members are individuals, of varying majors, with career goals in the criminal justice system such as law enforcement, probation, corrections, security, and law. The primary objectives of the Fraternity are to assist members with occupational preparation, career selection, career acquisition and to provide a fertile environment for academic study. Tau Rho Kappa also supports and promotes the Department of Justice Studies, strives to improve the campus environment, and makes positive contributions to the local community. Learn more about us!</p>
  </div>
  <div class="abs btn-out welcome-btn">Learn More →</div>
  <div class="abs divider"></div>
  <div class="abs social-label">Visit ΤΡΚ On Social Media</div>
  <div class="abs socials welcome-social" aria-label="Social media links"><span></span><span></span><span></span><span></span></div>
  <div class="frame" style="left:695px;top:722px;width:377px;height:304px"></div>
  <div class="photo" style="left:679px;top:705px;width:377px;height:309px;background:linear-gradient(180deg,#8d8f94,#3a2f33)" role="img" aria-label="Group photo of fraternity members standing in front of a building entrance"></div>
</section>

<section class="strip">
  <div class="photo" style="left:0;top:1216px;width:212px;height:326px;background:linear-gradient(160deg,#bdbdbd,#3c3c3c)" role="img" aria-label="Black and white photo of students studying outdoors with laptops"></div>
  <div class="photo" style="left:240px;top:1258px;width:225px;height:324px;background:linear-gradient(180deg,#b4452c,#8a2613)" role="img" aria-label="Red toned photo of students"></div>
  <div class="abs serif strip-word">Prudence</div>
  <div class="photo" style="left:493px;top:1216px;width:224px;height:326px;background:linear-gradient(180deg,#d0d0d0,#6d6d6d)" role="img" aria-label="Black and white photo of students talking in a classroom"></div>
  <div class="photo" style="left:745px;top:1258px;width:225px;height:324px;background:linear-gradient(180deg,#1a1a1a,#6e6e6e)" role="img" aria-label="Black and white photo of a cheering crowd with raised hands"></div>
  <div class="photo" style="left:996px;top:1216px;width:204px;height:326px;background:linear-gradient(180deg,#9a9a9a,#2e2e2e)" role="img" aria-label="Black and white photo of graduates tossing caps in the air"></div>
</section>

<section>
  <div class="abs careers"></div>
  <h2 class="abs serif careers-h">ΤΡΚ CRIMINAL JUSTICE ALUMNI CAREERS</h2>

  <div class="card" style="left:228px;top:1742px">
    <svg width="34" height="40" viewBox="0 0 34 40" fill="none" stroke="#222" stroke-width="1.6"><path d="M6 12h22M9 12l2-8h12l2 8"/><rect x="10" y="14" width="14" height="6" rx="2"/><path d="M4 38c0-9 6-13 13-13s13 4 13 13"/><path d="M17 25v13"/></svg>
    <p>SPECIAL AGENT</p>
  </div>
  <div class="card" style="left:616px;top:1742px">
    <svg width="40" height="40" viewBox="0 0 40 40" fill="none" stroke="#222" stroke-width="1.6"><rect x="14" y="4" width="10" height="16" rx="1" transform="rotate(45 19 12)"/><path d="M22 17l12 12"/><path d="M4 36h20M7 32h14"/></svg>
    <p>PROBATION/PAROLE</p>
  </div>
  <div class="card" style="left:228px;top:1907px">
    <svg width="36" height="40" viewBox="0 0 36 40" fill="none" stroke="#222" stroke-width="1.6"><path d="M18 3l14 5v11c0 9-6 15-14 18C10 34 4 28 4 19V8z"/><path d="M18 8l9 3v8c0 6-4 10-9 12-5-2-9-6-9-12v-8z"/></svg>
    <p>PRIVATE SECURITY/INTELLIGENCE</p>
  </div>
  <div class="card" style="left:616px;top:1907px">
    <svg width="36" height="40" viewBox="0 0 36 40" fill="none" stroke="#222" stroke-width="1.6"><path d="M18 3c4 3 8 4 13 4v13c0 8-6 14-13 17C11 34 5 28 5 20V7c5 0 9-1 13-4z"/><path d="M18 12l2.3 4.6 5 .7-3.6 3.5.9 5-4.6-2.4-4.6 2.4.9-5-3.6-3.5 5-.7z"/></svg>
    <p>LOCAL/STATE LAW ENFORCEMENT</p>
  </div>
  <div class="card" style="left:228px;top:2070px">
    <svg width="40" height="40" viewBox="0 0 40 40" fill="none" stroke="#222" stroke-width="1.6"><path d="M20 4v30M8 10h24M12 36h16"/><path d="M8 10l-5 12h10zM32 10l-5 12h10z"/><path d="M3 22a5 4 0 0 0 10 0M27 22a5 4 0 0 0 10 0"/></svg>
    <p>LAWYER</p>
  </div>
  <div class="card" style="left:616px;top:2070px">
    <svg width="36" height="40" viewBox="0 0 36 40" fill="none" stroke="#222" stroke-width="1.6"><rect x="5" y="5" width="20" height="28" rx="1"/><path d="M10 3h10v5H10zM9 14h12M9 19h8"/><circle cx="24" cy="27" r="6"/><path d="M28.5 31.5l5 5"/></svg>
    <p>DA INVESTIGATOR</p>
  </div>
</section>

<section>
  <div class="photo" style="left:0;top:2273px;width:1200px;height:437px;background:linear-gradient(180deg,#a9a4a8,#6a6468 60%,#4f4a4e)" role="img" aria-label="Black and white group photo of uniformed police officers standing in rows"></div>
  <div class="abs officers-text"><span class="script">Our Alumni Are</span> <span class="serif">OFFICERS</span></div>
</section>

<section>
  <div class="abs support"></div>
  <h2 class="abs serif h-wide support-h">SUPPORT OUR ΤΡΚ</h2>
  <p class="abs p support-p">Help our organization by donating today! All donations go directly to making a difference for our cause.</p>
  <div class="abs btn-red donate">Donate Now →</div>
  <div class="frame" style="left:623px;top:2788px;width:442px;height:290px"></div>
  <div class="photo" style="left:602px;top:2771px;width:443px;height:290px;background:linear-gradient(160deg,#b79a86,#6f6f78)" role="img" aria-label="Group of smiling members wearing grey fraternity sweatshirts"></div>
</section>

<section>
  <h2 class="abs serif h-wide contact-h">GET IN TOUCH</h2>
  <p class="abs p contact-p">Have questions or want to join our vibrant community? Drop<br>us a line or send us a message and we'll get back to you!</p>
  <div class="abs form"></div>
  <div class="field" style="top:3395px">Full Name *</div>
  <div class="field" style="top:3450px">Email Address *</div>
  <div class="field" style="top:3505px">Phone Number *</div>
  <div class="field" style="top:3562px">Your Message *</div>
  <div class="abs btn-red send">SEND ✉</div>
</section>

<section>
  <div class="abs alumni"></div>
  <div class="photo" style="left:144px;top:3813px;width:454px;height:357px;background:linear-gradient(135deg,#c9b08d,#7fb8d6 45%,#6d5a4a)" role="img" aria-label="Collage of vintage alumni group photos around a pentagon-shaped centre photo"></div>
  <h2 class="abs serif alumni-h">ALUMNI</h2>
  <p class="abs p alumni-p">I want to welcome you to the new Tau Rho Kappa Fraternity website. The public section is primarily for the use of the active Fraternity members to help them recruit new members and make available their calendar of events. The Alumni section is only available to active alumni with good standing. We welcome comments and suggestions on other topics to be included and on ways to improve our website.</p>
  <div class="abs sign" style="top:4072px">Daniel Moreno</div>
  <div class="abs sign" style="top:4094px">Alumni President</div>
  <div class="abs btn-out alumni-btn">Learn More →</div>
</section>

<footer>
  <div class="abs footer"></div>
  <div class="abs foot-mark"></div>
  <div class="abs serif foot-name">ΤΡΚ</div>
  <div class="foot-col" style="left:272px"><h4>VISIT US</h4><p>418 North Alder Avenue<br>Ferndale Ridge, California</p></div>
  <div class="foot-col" style="left:505px"><h4>CONTACT US</h4><p>info@taurhokappa.org</p></div>
  <div class="foot-col" style="left:733px"><h4>FOLLOW US</h4><div class="socials" aria-label="Social media links"><span></span><span></span><span></span><span></span></div></div>
</footer>

</body>
</html>
```